Tellmora Corporate Stationery

Look for design of all new corporate stationery for an existing insurance broking business that is going through a redesign and move from older partners to younger family members. New Logo is attached. Company is Brisbane based.
Colours in the Logo is Hex #43bed8 and website features a lot of hex #17b8d8. Website front page "A plan to protect you" - headline. "Professional and Individual advice to protect your greatest assets" - tagline.

Stationery required: Business Cards, Letter head, Thank-you cards, Birthday cards, Presentation folders, With Compliment slips and a powerpoint template. We also would like to send a card to all customers with the something along of the lines of "something new".

Target Market(s)

Customers of Insurance business looking at superannuation, life and income protection insurance, investment advice and wills

Industry/Entity Type

Insurance Broker

Font styles to use
Other font styles liked:
• same as logo

Requirements
Must have
• The above designs for new stationery for the new business including:
• Business Cards, Letter head, Thank-you cards, Birthday cards, Presentation folders, With Compliment slips and a powerpoint template. We also would like to send a card to all customers with the something along of the lines of "something new".
Nice to have
• It is a new look - long time family business being passed to next generation - big focus on advice for YOU, individual advice etc..

```html
<!DOCTYPE html>
<html lang="en">
<head>
<meta charset="utf-8">
<title>Tellmora Business Card</title>
<link rel="stylesheet" href="https://fonts.googleapis.com/css2?family=Source+Sans+3:ital,wght@0,400;0,600;1,400&display=swap">
<style>
  :root {
    --brand-blue: #3dbdd8;
    --brand-grey: #85868a;
    --text-dark: #4a4a4c;
    --rule-grey: #9a9a9c;
    --card-white: #ffffff;
    --backdrop: #2b2b2c;
  }
  * { margin: 0; padding: 0; box-sizing: border-box; }
  html, body {
    width: 1200px; height: 987px; overflow: hidden;
    background: var(--backdrop);
    font-family: "Source Sans 3", sans-serif;
  }
  .canvas { position: relative; width: 1200px; height: 987px; }
  .card { position: absolute; width: 615px; height: 352px; overflow: hidden; }
  .card-front { left: 293px; top: 130px; background: var(--card-white); }
  .card-back { left: 292px; top: 505px; background: var(--brand-blue); }

  .brand-mark {
    position: absolute; right: 29px; top: 64px;
    display: flex; align-items: center; gap: 12px;
  }
  .brand-dot { width: 40px; height: 40px; border-radius: 50%; background: var(--brand-blue); }
  .brand-name {
    font-size: 38px; font-weight: 600; color: var(--brand-blue);
    letter-spacing: 1px; text-transform: uppercase; line-height: 1;
  }

  .holder-name {
    position: absolute; left: 26px; top: 162px;
    font-size: 23px; font-weight: 600; color: var(--brand-blue); line-height: 1;
  }
  .holder-title {
    position: absolute; left: 26px; top: 193px;
    font-size: 16px; color: var(--brand-grey); line-height: 1;
  }
  .divider {
    position: absolute; left: 26px; top: 216px; width: 560px; height: 1px;
    background: var(--rule-grey);
  }
  .contact-list {
    position: absolute; left: 27px; top: 224px; list-style: none;
  }
  .contact-item {
    display: flex; align-items: center; height: 23.5px;
    font-size: 16px; color: var(--text-dark);
  }
  .contact-icon { width: 16px; height: 16px; margin-right: 8px; fill: var(--brand-blue); }

  .address {
    position: absolute; right: 29px; top: 268px; text-align: right;
    font-size: 16px; line-height: 22px; color: var(--text-dark);
  }

  .footer-bands { position: absolute; left: 0; bottom: 0; width: 615px; height: 32px; }
  .footer-web {
    position: absolute; left: 372px; right: 0; bottom: 6px;
    text-align: center; font-size: 16px; letter-spacing: 2.5px; color: var(--card-white);
  }

  .back-pattern { position: absolute; inset: 0; background: var(--brand-blue); }
  .back-brand {
    position: absolute; left: 0; right: 0; top: 150px;
    display: flex; justify-content: center; align-items: center; gap: 10px;
  }
  .back-brand .brand-dot { width: 30px; height: 30px; background: var(--card-white); }
  .back-brand .brand-name { color: var(--card-white); font-size: 32px; }
  .back-web {
    position: absolute; left: 0; right: 0; top: 287px; text-align: center;
    font-size: 17px; font-style: italic; letter-spacing: 2.5px; color: var(--card-white);
  }
</style>
</head>
<body>
<main class="canvas">
  <section class="card card-front">
    <div class="brand-mark">
      <span class="brand-dot"></span>
      <span class="brand-name">Tellmora</span>
    </div>

    <h1 class="holder-name">LIAM CARVER</h1>
    <p class="holder-title">CEO/FOUNDER</p>
    <div class="divider"></div>

    <ul class="contact-list">
      <li class="contact-item">
        <svg class="contact-icon" viewBox="0 0 16 16"><path d="M3.6 1.2l2.3 2.6-1.3 2c.9 1.9 2.4 3.4 4.4 4.4l2-1.3 2.6 2.3-1.2 2.2C7.3 13.6 2.4 8.7 1.6 3.5z"/></svg>
        617 402 1185
      </li>
      <li class="contact-item">
        <svg class="contact-icon" viewBox="0 0 16 16"><path d="M4 1h8v14H4zM5.3 2.5v9.8h5.4V2.5zM7 13.2h2v.9H7z" fill-rule="evenodd"/></svg>
        617 559 3042
      </li>
      <li class="contact-item">
        <svg class="contact-icon" viewBox="0 0 16 16"><path d="M4 1.5h8v4H4zM1 6.5h14v6h-2.5v-2h-9v2H1zM4.5 11.5h7v3h-7z"/></svg>
        617 402 1190
      </li>
      <li class="contact-item">
        <svg class="contact-icon" viewBox="0 0 16 16"><path d="M1 3.5h14v9H1zM2.3 4.6L8 9l5.7-4.4z" fill-rule="evenodd"/></svg>
        liam@tellmora.com
      </li>
    </ul>

    <address class="address" style="font-style: normal;">
      48 Wattlebrook Road<br>
      Brisbane, Queensland 4000
    </address>

    <svg class="footer-bands" viewBox="0 0 615 32" preserveAspectRatio="none">
      <rect x="0" y="14" width="372" height="7" fill="var(--brand-grey)"/>
      <rect x="0" y="22" width="615" height="10" fill="var(--brand-blue)"/>
      <polygon points="376,0 615,0 615,32 356,32" fill="var(--brand-blue)"/>
    </svg>
    <p class="footer-web">www.tellmora.com</p>
  </section>

  <section class="card card-back">
    <div class="back-pattern" role="img" aria-label="Faint repeating brand pattern in light blue tones"></div>
    <div class="back-brand">
      <span class="brand-dot"></span>
      <span class="brand-name">Tellmora</span>
    </div>
    <p class="back-web">www.tellmora.com</p>
  </section>
</main>
</body>
</html>
```